Specialised investor in e-mobility and energy wants business card design

We need a business card design that fits our existing corporate design. <The look and feel must be 'sharp'/'clean', dynamic, communicate momentum, professionalism etc (as one would imagine from a firm in the financial sector). We like the idea of a reverse-side of the card that includes the logo, and the name and contact details on the other. We expect the deliverable to be whatever format might be required to be able to get cards printed directly by a service such as kelmo press. Our website is www.zub.capital

```html
<!DOCTYPE html>
<html lang="en">
<head>
<meta charset="utf-8">
<title>Zub Capital – Business Card</title>
<link rel="stylesheet" href="https://fonts.googleapis.com/css2?family=Montserrat:wght@400;500;700&display=swap">
<style>
  :root {
    --green-dark: #2e4d1e;
    --green-light: #8ab84a;
    --text-dark: #333333;
    --card-bg: #ffffff;
    --page-bg: #e9e9e6;
  }
  * { margin: 0; padding: 0; box-sizing: border-box; }
  html, body { width: 900px; height: 1200px; overflow: hidden; }
  body {
    background: var(--page-bg);
    position: relative;
    font-family: "Montserrat", sans-serif;
    color: var(--text-dark);
  }
  .card {
    position: absolute;
    left: 80px;
    width: 742px;
    height: 440px;
    background: var(--card-bg);
    border-radius: 36px;
    overflow: hidden;
    box-shadow: 0 2px 6px rgba(0,0,0,0.18);
  }
  .card--front { top: 132px; }
  .card--back { top: 638px; }

  .brand-name {
    position: absolute;
    font-family: "Montserrat", sans-serif;
    font-weight: 500;
    color: var(--green-dark);
    white-space: nowrap;
    line-height: 1;
  }
  .card--front .brand-name { left: 26px; top: 214px; font-size: 54px; }
  .card--back .brand-name { left: 0; right: 0; text-align: center; top: 176px; font-size: 88px; }

  .divider {
    position: absolute;
    left: 406px; top: 140px;
    width: 2px; height: 188px;
    background: var(--green-light);
  }
  .contact { position: absolute; left: 461px; top: 138px; }
  .contact__name { font-size: 27px; font-weight: 700; color: var(--green-dark); line-height: 1.1; }
  .contact__role { font-size: 16px; margin-top: 2px; }
  .contact__list { list-style: none; margin-top: 22px; font-size: 16px; }
  .contact__list li { display: flex; align-items: center; gap: 10px; height: 22px; }
  .contact__list svg { width: 13px; height: 13px; fill: var(--green-light); flex: none; }
  .contact__address { margin-top: 16px; font-size: 16px; line-height: 1.3; }

  .footer-stripe {
    position: absolute;
    left: 0; right: 0; bottom: 46px;
    height: 6px;
    background: var(--green-light);
  }
  .footer-band {
    position: absolute;
    left: 0; right: 0; bottom: 0;
    height: 40px;
    background: var(--green-dark);
  }
</style>
</head>
<body>
  <section class="card card--front">
    <div class="brand-name">Zub Capital</div>
    <div class="divider"></div>
    <div class="contact">
      <div class="contact__name">Mark Halvorsen</div>
      <div class="contact__role">Owner</div>
      <ul class="contact__list">
        <li><svg viewBox="0 0 16 16" aria-hidden="true"><path d="M3 2h3l1.5 3.5-2 1.3a8 8 0 0 0 3.7 3.7l1.3-2L14 10v3a1 1 0 0 1-1 1A11 11 0 0 1 2 3a1 1 0 0 1 1-1z"/></svg>+41 79555 0147</li>
        <li><svg viewBox="0 0 16 16" aria-hidden="true"><path d="M1 3h14v10H1z"/><path d="M1 3l7 6 7-6" fill="none" stroke="#ffffff" stroke-width="1.4"/></svg>mark@zub.capital</li>
        <li><svg viewBox="0 0 16 16" aria-hidden="true"><circle cx="8" cy="8" r="7"/><path d="M1 8h14M8 1c-3 3-3 11 0 14M8 1c3 3 3 11 0 14" fill="none" stroke="#ffffff" stroke-width="1"/></svg>www.zub.capital</li>
      </ul>
      <div class="contact__address">48 Meridian Road, Suite 210<br>Alder Falls, PA 19001</div>
    </div>
    <div class="footer-stripe"></div>
    <div class="footer-band"></div>
  </section>

  <section class="card card--back">
    <div class="brand-name">Zub Capital</div>
  </section>
</body>
</html>
```